Maple Gable Business Card

Colors can be blue, grey and white as you see in the attached logo. Needs to have a spot for name, title, phone, email, address, and website. There also needs to be a spot for an agent's picture.

Contact Information for Business Card

See project description.

Colors

Designer to choose colors to be used in the design.

```html
<!DOCTYPE html>
<html lang="en">
<head>
<meta charset="utf-8">
<title>Maple Gable Business Card</title>
<link rel="stylesheet" href="https://fonts.googleapis.com/css2?family=Montserrat:wght@600&family=Roboto:wght@400;500&display=swap">
<style>
  :root {
    --page-bg: #a6a6a6;
    --card-white: #ffffff;
    --brand-blue: #2a78b8;
    --name-blue: #1f6cb0;
    --card-grey: #58585a;
    --text-grey: #555558;
    --text-dark: #3c3c3e;
    --photo-light: #d9e4ee;
    --photo-dark: #a9bccd;
  }
  * { box-sizing: border-box; margin: 0; padding: 0; }
  html, body {
    width: 1200px; height: 954px; overflow: hidden;
    background: var(--page-bg);
    font-family: "Roboto", Arial, sans-serif;
  }
  .card {
    position: absolute; top: 342px;
    width: 524px; height: 298px;
    box-shadow: 0 4px 8px rgba(0,0,0,0.25);
    overflow: hidden;
  }
  .card--front { left: 68px; background: var(--card-white); }
  .card--back { left: 603px; background: var(--card-grey); }

  .front__band {
    position: absolute; top: 0; right: 0;
    width: 246px; height: 100%;
    background: var(--brand-blue);
  }
  .agent__photo {
    position: absolute; left: 48px; top: 44px;
    width: 150px; height: 210px;
    border: 4px solid var(--card-white);
    background: linear-gradient(160deg, var(--photo-light), var(--photo-dark));
  }
  .wordmark {
    font-family: "Montserrat", Arial, sans-serif;
    font-weight: 600; letter-spacing: 0.5px; white-space: nowrap;
  }
  .front__wordmark {
    position: absolute; left: 27px; top: 40px;
    font-size: 21px; color: var(--name-blue);
  }
  .agent__name {
    position: absolute; left: 27px; top: 119px;
    font-weight: 500; font-size: 20px; color: var(--name-blue);
  }
  .agent__title {
    position: absolute; left: 27px; top: 144px;
    font-size: 15px; color: var(--text-dark);
  }
  .agent__address {
    position: absolute; left: 27px; top: 171px;
    font-size: 14.5px; line-height: 19px; color: var(--text-grey);
  }
  .contact-list {
    position: absolute; left: 27px; top: 220px;
    list-style: none; font-size: 14.5px; color: var(--text-dark);
  }
  .contact-list li {
    display: flex; align-items: center; gap: 7px; height: 19px;
  }
  .contact-list svg { width: 13px; height: 13px; fill: var(--name-blue); }
  .contact-list .accent { color: var(--name-blue); }

  .back__logo {
    position: absolute; right: 38px; top: 228px;
    display: flex; align-items: center; gap: 9px;
  }
  .back__mark { width: 14px; height: 14px; background: var(--card-white); }
  .back__wordmark { font-size: 23px; color: var(--card-white); }
</style>
</head>
<body>
  <section class="card card--front">
    <div class="wordmark front__wordmark">MAPLE GABLE</div>
    <div class="agent__name">Daniel Reyes</div>
    <div class="agent__title">Manager</div>
    <div class="agent__address">Your address, city<br>state, ZIP 0000</div>
    <ul class="contact-list">
      <li>
        <svg viewBox="0 0 24 24"><path d="M6.6 10.8a15 15 0 0 0 6.6 6.6l2.2-2.2c.3-.3.7-.4 1-.2 1.1.4 2.3.6 3.6.6.6 0 1 .4 1 1V20c0 .6-.4 1-1 1A17 17 0 0 1 3 4c0-.6.4-1 1-1h3.5c.6 0 1 .4 1 1 0 1.3.2 2.5.6 3.6.1.3 0 .7-.2 1z"/></svg>
        555-014-2100
      </li>
      <li>
        <svg viewBox="0 0 24 24"><path d="M2 5h20v14H2z"/><path d="M2 5l10 8 10-8v1.5l-10 8-10-8z" fill="#fff"/></svg>
        daniel@maplegable.com
      </li>
      <li>
        <svg viewBox="0 0 24 24"><circle cx="12" cy="12" r="10"/><path d="M2 12h20M12 2c3 3 3 17 0 20M12 2c-3 3-3 17 0 20" stroke="#fff" stroke-width="1.5" fill="none"/></svg>
        <span>www.<span class="accent">maplegable</span>.com</span>
      </li>
    </ul>
    <div class="front__band">
      <div class="agent__photo" role="img" aria-label="Agent portrait photo"></div>
    </div>
  </section>

  <section class="card card--back">
    <div class="back__logo">
      <span class="back__mark"></span>
      <span class="wordmark back__wordmark">MAPLE GABLE</span>
    </div>
  </section>
</body>
</html>
```